Children’s entertainer/balloon artist Website Home Page and custom landing page

I need a home page design for the home page of a children and family entertainer/balloon twister’s website. I also need a custom landing page for family theatre shows performed by the same entertainer.
It will be a Wordpress website and I need the final artwork in a layer Photoshop file with all the layers clearly named and labeled.

Target Market(s)

The site visitors are mainly mums, aged between early 20’s and late 30’s. Other visitors will included companies for Christmas functions, and event organisers for corporate functions.

Industry/Entity Type

Entertainment

Number of Pages Required

2 page

Font styles to use
Sans Serif

Colors
34a6d7
f37122

Requirements
Must have
• Layout
• I have included a wireframe for the home page layout and the custom landing page for your reference. This is a guide only and I welcome your interpretation with the rough layout provided.
• This website needs to look good on all devices as it will be fully responsive.
• It needs to include a footer area on the page, that has social media and a call to action area included.
• Colours
• The main colours for the site is:
• orange (call to action colour)
• ff6800
• blue/turquoise
• 42abc3
• Pictures
• I have included images of the entertainer/balloon artist for you to use/take inspiration from.
• These images will be included on the website. I want to show lots of people having fun.
• I would like to have elements of the logo used in isolation across the website
• i.e. the octopus figure to be included in the footer or the bird element to be included in the testimonial slider etc.
• Elements to include
• Note: use the images of the entertainer in the boxes on the home page (balloon shows, balloon twisting, balloon workshops, theatre shows (the three little balloon pigs on his head)
Nice to have
Should not have
• Element to avoid
• Stock imagery of balloon sculptures - use images provided.

```html
<!DOCTYPE html>
<html lang="en">
<head>
<meta charset="utf-8">
<title>Benny Bounce – Balloon Shows &amp; Family Entertainment</title>
<link href="https://fonts.googleapis.com/css2?family=Open+Sans:ital,wght@0,400;0,600;0,700;0,800;1,700;1,800&display=swap" rel="stylesheet">
<style>
:root{
  --blue:#34a6d7;
  --blue-dark:#1f7fb0;
  --blue-deep:#0f4f78;
  --footer:#15557f;
  --footer-bar:#0d3f60;
  --orange:#f37122;
  --orange-bright:#ff6800;
  --ink:#4a4a4a;
  --muted:#8a8a8a;
  --line:#e3e3e3;
  --paper:#ffffff;
  --soft:#f4f6f7;
}
*{box-sizing:border-box;margin:0;padding:0}
html,body{width:705px;height:1200px;overflow:hidden}
body{font-family:"Open Sans",Arial,sans-serif;color:var(--ink);background:var(--paper);position:relative;font-size:9px;line-height:1.45}
.page{position:relative;width:705px;height:1200px;overflow:hidden}

/* header */
.hero-band{position:absolute;left:0;top:40px;width:705px;height:300px;background:linear-gradient(180deg,var(--blue) 0%,#4cb6e2 60%,var(--blue-dark) 100%)}
.topbar{position:absolute;left:0;top:0;width:705px;height:100px;background:var(--paper);border-bottom:3px solid #d9eef8}
.logo{position:absolute;left:22px;top:4px;width:160px;height:150px;z-index:5;display:flex;align-items:flex-end;justify-content:center}
.logo-art{position:absolute;inset:0 0 36px 0;border-radius:12px;background:linear-gradient(160deg,#f6c58c,#d98a3a 55%,#3a8fc6)}
.logo-name{position:relative;background:var(--paper);padding:4px 8px;font-weight:800;font-size:19px;color:var(--orange);border-radius:4px}
.social-top{position:absolute;left:458px;top:12px;display:flex;gap:5px}
.social-top span{width:20px;height:20px;border-radius:50%;background:#e0403a;display:block}
.call{position:absolute;left:540px;top:12px;font-size:15px;font-weight:700;color:var(--orange)}
.call small{font-size:12px;color:var(--blue-dark);font-weight:600}
.nav{position:absolute;left:220px;top:60px;display:flex;gap:4px;font-size:10.5px;font-weight:600}
.nav a{color:var(--ink);text-decoration:none;padding:7px 12px}
.nav a.active{background:var(--blue);color:#fff;border-radius:3px}

.slider{position:absolute;left:104px;top:120px;width:496px;height:230px;border:5px solid #fff;box-shadow:0 6px 14px rgba(0,0,0,.25);background:linear-gradient(135deg,#cfc6b5,#e8dfcf 40%,#f1a8b8 70%,#b99a8a)}
.slider-title{position:absolute;left:22px;top:78px;color:#fff;font-size:25px;line-height:1.2;font-weight:800;font-style:italic;text-shadow:0 2px 4px rgba(0,0,0,.45)}
.slider-dots{position:absolute;left:50%;bottom:8px;transform:translateX(-50%);display:flex;gap:5px}
.slider-dots span{width:7px;height:7px;border-radius:50%;background:rgba(255,255,255,.6)}
.slider-dots span:first-child{background:var(--orange)}

/* testimonials */
.section-title{font-size:15px;font-weight:600;color:var(--muted)}
.section-title b{color:var(--blue-dark);font-weight:700}
.testimonials{position:absolute;left:70px;top:368px;width:440px}
.testimonials .rule{height:1px;background:var(--line);margin:6px 0 12px}
.quote{display:flex;gap:14px;align-items:flex-start}
.avatar{width:46px;height:46px;border-radius:50%;background:linear-gradient(#c9d6de,#8fa4b2);flex:none}
.quote p{font-size:8.5px;color:var(--muted)}
.promo{position:absolute;left:520px;top:360px;width:150px;height:160px;border-radius:8px;background:linear-gradient(180deg,#e4f3fb,#8fcbea 60%,var(--blue))}
.promo-note{position:absolute;left:6px;bottom:44px;width:138px;text-align:center;color:#fff;font-size:9px;font-weight:700}
.btn{display:inline-block;background:var(--orange);color:#fff;font-weight:700;font-size:11px;padding:5px 12px;border-radius:3px;text-decoration:none}
.promo .btn{position:absolute;left:36px;bottom:12px}

/* welcome */
.welcome{position:absolute;left:70px;top:528px;width:390px}
.welcome h2{font-size:14px;font-weight:600;color:var(--blue-dark);margin-bottom:8px}
.welcome h2 span{color:var(--orange)}
.welcome p{font-size:8px;color:var(--muted);margin-bottom:7px}
.welcome p a{color:var(--orange);text-decoration:none}
.friends{position:absolute;left:482px;top:528px;width:200px;height:135px;border:1px solid var(--line);background:var(--paper);padding:8px}
.friends-head{display:flex;gap:8px;align-items:center;font-size:8.5px;font-weight:700;color:var(--ink);margin-bottom:8px}
.friends-head i{width:26px;height:26px;background:#b8c8d2;display:block}
.friends-grid{display:grid;grid-template-columns:repeat(4,1fr);gap:6px}
.friends-grid i{height:34px;background:linear-gradient(#d9e1e6,#9eb0bc);display:block}

/* services */
.services-band{position:absolute;left:0;top:690px;width:705px;height:230px}
.services-band svg{position:absolute;left:0;top:0}
.cards{position:absolute;left:93px;top:738px;display:flex;gap:14px}
.card{width:119px;background:var(--paper);border:3px solid var(--paper);box-shadow:0 4px 10px rgba(0,0,0,.25);position:relative}
.card h3{font-size:11px;font-weight:700;color:#fff;text-align:center;padding:3px 0 4px;background:transparent;position:absolute;top:-22px;left:0;width:100%}
.card h3 em{color:var(--orange);font-style:normal}
.card-photo{height:80px}
.card p{background:var(--blue);color:#fff;font-size:7px;padding:6px;height:60px}
.card-foot{height:16px;background:var(--blue);position:relative}
.card-foot::after{content:"";position:absolute;left:50%;bottom:-10px;transform:translateX(-50%);border:10px solid transparent;border-top-color:var(--blue);border-bottom:0}
.c1 .card-photo{background:linear-gradient(135deg,#f07a9b,#7fc6e6)}
.c2 .card-photo{background:linear-gradient(135deg,#f2c24a,#5a9fd1)}
.c3 .card-photo{background:linear-gradient(135deg,#4b8ed0,#f5d36a)}
.c4 .card-photo{background:linear-gradient(135deg,#f39fb8,#3f7fb9)}

/* cta */
.cta{position:absolute;left:70px;top:944px;width:480px;height:60px;background:var(--orange);clip-path:polygon(0 0,100% 0,94% 100%,0 100%);display:flex;align-items:center;gap:18px;padding:0 24px}
.cta p{color:#fff;font-size:13px;font-weight:600;line-height:1.3}
.cta .btn{background:#fff;color:var(--orange);flex:none}
.cta-mascot{position:absolute;left:565px;top:912px;width:100px;height:104px;border-radius:10px;background:linear-gradient(160deg,#f6c58c,#d98a3a 55%,#3a8fc6)}

/* footer */
.footer{position:absolute;left:0;top:1020px;width:705px;height:168px;background:var(--footer);color:#cfe3ef;padding:18px 70px 0;display:grid;grid-template-columns:1fr 1fr 1fr 1fr;gap:16px}
.footer h4{color:#fff;font-size:11px;font-weight:600;margin-bottom:8px;padding-bottom:5px;border-bottom:1px solid rgba(255,255,255,.2)}
.footer ul{list-style:none;font-size:8px;line-height:1.9}
.field{height:14px;background:#fff;border-radius:2px;margin-bottom:5px;font-size:7px;color:#999;padding:2px 4px}
.field.area{height:26px}
.footer .btn{font-size:8px;padding:3px 8px}
.detail{display:flex;gap:6px;align-items:flex-start;font-size:8px;margin-bottom:6px}
.detail svg{flex:none;margin-top:1px}
.follow li{display:flex;align-items:center;gap:6px;margin-bottom:4px}
.follow i{width:14px;height:14px;background:#2c79aa;border-radius:2px;display:block}
.bottom-bar{position:absolute;left:0;top:1188px;width:705px;height:12px;background:var(--footer-bar);color:#8fb3c9;font-size:6.5px;padding-left:70px;line-height:12px}
</style>
</head>
<body>
<div class="page">

  <div class="hero-band"></div>

  <header class="topbar">
    <nav class="nav">
      <a class="active" href="#">Home</a>
      <a href="#">Balloon Shows</a>
      <a href="#">Balloon Decoration</a>
      <a href="#">Theatre</a>
      <a href="#">Reviews</a>
      <a href="#">Contact</a>
    </nav>
    <div class="social-top"><span></span><span></span><span></span></div>
    <div class="call"><small>Call Now</small> 555-0142-88</div>
  </header>

  <div class="logo">
    <div class="logo-art" role="img" aria-label="Cartoon entertainer mascot with balloons"></div>
    <span class="logo-name">Benny Bounce</span>
  </div>

  <section class="slider" role="img" aria-label="Entertainer wearing three pink balloon pigs on his head">
    <h1 class="slider-title">Hilarious funny balloon<br>shows &amp; balloon<br>twisting</h1>
    <div class="slider-dots"><span></span><span></span><span></span></div>
  </section>

  <section class="testimonials">
    <h2 class="section-title">Client <b>Testimonials</b></h2>
    <div class="rule"></div>
    <div class="quote">
      <div class="avatar" role="img" aria-label="Client portrait"></div>
      <p>Benny made our daughter's party the best day ever. The children laughed from start to finish and every guest went home with a balloon animal. We will book him again next year without a doubt.</p>
    </div>
  </section>

  <aside class="promo" role="img" aria-label="Mascot figure holding a sign">
    <div class="promo-note">Book Benny for Your Next Function</div>
    <a class="btn" href="#">Book Now</a>
  </aside>

  <section class="welcome">
    <h2>Welcome to <span>Benny Bounce</span></h2>
    <p>Benny is a family entertainer and balloon artist bringing laughter to birthday parties, school events and festivals. His shows mix comedy, magic and giant balloon creations that get every child joining in. Parents relax while the kids have the time of their lives, and every show is tailored to the age of the audience.</p>
    <p>From small garden parties to large corporate Christmas functions, Benny brings the fun to you with balloon twisting, workshops and theatre shows for all ages. <a href="#">Read More</a></p>
  </section>

  <aside class="friends">
    <div class="friends-head"><i></i>Benny Bounce<br>Fans and friends</div>
    <div class="friends-grid">
      <i></i><i></i><i></i><i></i><i></i><i></i><i></i><i></i>
    </div>
  </aside>

  <section class="services-band">
    <svg width="705" height="230" viewBox="0 0 705 230" aria-hidden="true">
      <path d="M0 30 Q352 -10 705 30 L705 200 Q352 240 0 200 Z" fill="#34a6d7"/>
      <path d="M0 150 Q352 120 705 160 L705 200 Q352 240 0 200 Z" fill="#1f7fb0" opacity=".5"/>
    </svg>
  </section>

  <div class="cards">
    <article class="card c1">
      <h3>Balloon <em>Shows</em></h3>
      <div class="card-photo" role="img" aria-label="Children watching a balloon show"></div>
      <p>Funny interactive balloon shows packed with giggles, games and giant balloon surprises.</p>
      <div class="card-foot"></div>
    </article>
    <article class="card c2">
      <h3>Balloon <em>Twisting</em></h3>
      <div class="card-photo" role="img" aria-label="Entertainer twisting balloon animals for kids"></div>
      <p>Colourful balloon animals and hats twisted on the spot for every guest at your event.</p>
      <div class="card-foot"></div>
    </article>
    <article class="card c3">
      <h3>Balloon <em>Workshops</em></h3>
      <div class="card-photo" role="img" aria-label="Kids making balloon models in a workshop"></div>
      <p>Hands-on workshops where children learn to make their own balloon models to take home.</p>
      <div class="card-foot"></div>
    </article>
    <article class="card c4">
      <h3>Theatre <em>Shows</em></h3>
      <div class="card-photo" role="img" aria-label="Entertainer on stage with balloon pigs"></div>
      <p>Family theatre shows full of story, comedy and balloon characters for all ages.</p>
      <div class="card-foot"></div>
    </article>
  </div>

  <section class="cta">
    <p>Contact Now for More Detail and make your<br>Next Functions memorable</p>
    <a class="btn" href="#">Book Now</a>
  </section>
  <div class="cta-mascot" role="img" aria-label="Cartoon entertainer mascot"></div>

  <footer class="footer">
    <div>
      <h4>Quick Links</h4>
      <ul>
        <li>Home</li><li>Balloon Shows</li><li>Balloon Decoration</li><li>Theatre</li><li>Reviews</li><li>Contact</li>
      </ul>
    </div>
    <div>
      <h4>Contact Now</h4>
      <div class="field">Name</div>
      <div class="field">Email</div>
      <div class="field area">Message</div>
      <a class="btn" href="#">Submit</a>
    </div>
    <div>
      <h4>Contact Detail</h4>
      <div class="detail">
        <svg width="9" height="11" viewBox="0 0 9 11"><path d="M4.5 0A4 4 0 0 0 .5 4c0 3 4 7 4 7s4-4 4-7a4 4 0 0 0-4-4zm0 5.5a1.5 1.5 0 1 1 0-3 1.5 1.5 0 0 1 0 3z" fill="#fff"/></svg>
        <span><b style="color:#fff">Benny Bounce</b><br>12 Party Lane<br>Funtown, FT1 2AB</span>
      </div>
      <div class="detail">
        <svg width="10" height="10" viewBox="0 0 10 10"><path d="M2 0l2 2.5-1 1.2a6 6 0 0 0 3.3 3.3l1.2-1L10 8l-1.5 2C4 10 0 6 0 1.5z" fill="#fff"/></svg>
        <span>Phone: 555-0142-88</span>
      </div>
      <div class="detail">
        <svg width="10" height="8" viewBox="0 0 10 8"><rect width="10" height="8" rx="1" fill="#fff"/><path d="M0 0l5 4 5-4" stroke="#15557f" fill="none"/></svg>
        <span>hello@bennybounce.example</span>
      </div>
    </div>
    <div>
      <h4>Follow Us</h4>
      <ul class="follow">
        <li><i></i>Friendwall</li>
        <li><i></i>Chirper</li>
        <li><i></i>Worklink</li>
      </ul>
    </div>
  </footer>
  <div class="bottom-bar">Copyright © 2015 Benny Bounce. All rights reserved.</div>

</div>
</body>
</html>
```